Tall Fern Roofing Business Card

Need a business card with the logo that was designed here

Contact Information for Business Card

Name, Title, Phone, Email, Website, Company name

```html
<!DOCTYPE html>
<html lang="en">
<head>
<meta charset="utf-8">
<title>Tall Fern Roofing Business Card</title>
<link href="https://fonts.googleapis.com/css2?family=Open+Sans:wght@400;600;700&display=swap" rel="stylesheet">
<style>
  :root {
    --brand-blue: #1b74bd;
    --brand-grey: #939598;
    --ink: #2b2b2b;
    --paper: #ffffff;
    --backdrop: #e6e7e9;
  }
  * { box-sizing: border-box; margin: 0; padding: 0; }
  html, body { width: 1200px; height: 801px; overflow: hidden; }
  body {
    background: var(--backdrop);
    font-family: "Open Sans", Arial, sans-serif;
    color: var(--ink);
    position: relative;
  }
  .card {
    position: absolute;
    top: 240px;
    width: 560px;
    height: 320px;
    background: var(--paper);
    border-radius: 18px;
    overflow: hidden;
    box-shadow: 0 6px 18px rgba(0,0,0,0.12);
  }
  .card--back { left: 20px; }
  .card--front { left: 620px; border-bottom: 3px solid var(--brand-blue); }

  .wordmark {
    position: absolute;
    display: flex;
    align-items: center;
    gap: 10px;
    color: var(--brand-blue);
    font-weight: 700;
    white-space: nowrap;
  }
  .wordmark__square {
    background: var(--brand-blue);
    flex: none;
  }
  .card--back .wordmark { left: 30px; top: 128px; font-size: 22px; }
  .card--back .wordmark__square { width: 14px; height: 14px; }
  .card--front .wordmark {
    left: 0; right: 0; top: 136px;
    justify-content: center;
    font-size: 40px;
  }
  .card--front .wordmark__square { width: 26px; height: 26px; }

  .divider {
    position: absolute;
    left: 268px;
    top: 42px;
    width: 2px;
    height: 150px;
    background: var(--brand-blue);
  }
  .contact {
    position: absolute;
    left: 292px;
    top: 40px;
    line-height: 1.35;
  }
  .contact__name {
    color: var(--brand-blue);
    font-weight: 700;
    font-size: 20px;
    letter-spacing: 0.5px;
  }
  .contact__title { font-size: 13px; margin-bottom: 14px; }
  .contact__address { font-size: 13px; margin-bottom: 14px; }
  .contact__list { list-style: none; font-size: 13px; }
  .contact__list li { display: flex; align-items: center; gap: 8px; }
  .contact__icon { width: 12px; height: 12px; flex: none; fill: var(--brand-blue); }

  .swoosh { position: absolute; left: 0; bottom: 0; width: 560px; height: 120px; }
  .swoosh__grey { fill: var(--brand-grey); }
  .swoosh__blue { fill: var(--brand-blue); }
</style>
</head>
<body>
  <section class="card card--back" aria-label="Card back with contact details">
    <div class="wordmark">
      <span class="wordmark__square"></span>
      <span class="wordmark__name">Tall Fern Roofing</span>
    </div>
    <div class="divider"></div>
    <div class="contact">
      <p class="contact__name">DANA WHITLOCK</p>
      <p class="contact__title">Managing Director</p>
      <p class="contact__address">Your address, City<br>State, Zip 1234</p>
      <ul class="contact__list">
        <li>
          <svg class="contact__icon" viewBox="0 0 24 24" aria-hidden="true"><path d="M6.6 10.8a15.1 15.1 0 0 0 6.6 6.6l2.2-2.2a1 1 0 0 1 1-.25 11.4 11.4 0 0 0 3.6.57 1 1 0 0 1 1 1V20a1 1 0 0 1-1 1A17 17 0 0 1 3 4a1 1 0 0 1 1-1h3.5a1 1 0 0 1 1 1c0 1.25.2 2.45.57 3.6a1 1 0 0 1-.25 1z"/></svg>
          123 456 789
        </li>
        <li>
          <svg class="contact__icon" viewBox="0 0 24 24" aria-hidden="true"><path d="M2 5h20v14H2z M2 5l10 8 10-8" stroke="#fff" stroke-width="1.5"/></svg>
          info@yourgmail.com
        </li>
        <li>
          <svg class="contact__icon" viewBox="0 0 24 24" aria-hidden="true"><circle cx="12" cy="12" r="10"/><path d="M2 12h20M12 2c3 3 3 17 0 20M12 2c-3 3-3 17 0 20" stroke="#fff" stroke-width="1.4" fill="none"/></svg>
          www.yourwebsite.com
        </li>
      </ul>
    </div>
    <svg class="swoosh" viewBox="0 0 560 120" preserveAspectRatio="none" aria-hidden="true">
      <path class="swoosh__grey" d="M0 112 C 200 108, 420 70, 560 0 L 560 12 C 420 80, 200 116, 0 120 Z"/>
      <path class="swoosh__blue" d="M0 120 C 220 116, 430 80, 560 14 L 560 120 Z"/>
    </svg>
  </section>

  <section class="card card--front" aria-label="Card front with company name">
    <div class="wordmark">
      <span class="wordmark__square"></span>
      <span class="wordmark__name">Tall Fern Roofing</span>
    </div>
  </section>
</body>
</html>
```